RWT Fittings Ltd Business Cards

We need a business card with our business logo. We provide window and door installations on high-rises in west coast British Colombia, Canada.

I would like my business information and details on one side of the card, and the other side the company name with logo

Target Market(s)

General Contractors

Industry/Entity Type

Construction

Contact Information for Business Card

one side i want my company name and logo in the dark theme logo that i provided

Requirements
Must have
• Marco Peltieri, 16045518293, RWTFittings@mailbox-demo.com, 1407-5194 Linden Row Burnaby BC, V5H 2K9, Owner & Manager

```html
<!DOCTYPE html>
<html lang="en">
<head>
<meta charset="utf-8">
<title>RWT Fittings Ltd Business Cards</title>
<link rel="stylesheet" href="https://fonts.googleapis.com/css2?family=Raleway:wght@400;500;700&display=swap">
<style>
  :root {
    --stage: #2b2b2d;
    --blue-light: #1f9bd0;
    --blue-mid: #0d6f9c;
    --blue-deep: #064663;
    --brand-blue: #2f8fc4;
    --accent-blue: #1a9ad6;
    --paper: #f4f4f5;
    --paper-shade: #dcdcde;
    --ink-grey: #5a5a5c;
    --white: #ffffff;
  }
  * { box-sizing: border-box; margin: 0; padding: 0; }
  html, body {
    width: 1200px; height: 900px; overflow: hidden;
    background: var(--stage);
    font-family: "Raleway", sans-serif;
  }
  .canvas { position: relative; width: 1200px; height: 900px; }
  .card {
    position: absolute; left: 290px; width: 620px; height: 354px;
    overflow: hidden; box-shadow: 0 10px 28px rgba(0,0,0,.45);
  }

  /* Front */
  .card-front {
    top: 60px;
    background: radial-gradient(ellipse at 48% 45%, var(--blue-light) 0%, var(--blue-mid) 45%, var(--blue-deep) 100%);
    display: flex; align-items: center; justify-content: center;
  }
  .brand { display: flex; align-items: center; gap: 14px; font-weight: 700; letter-spacing: 1px; white-space: nowrap; }
  .card-front .brand { color: var(--white); font-size: 38px; }
  .brand-square { width: 40px; height: 40px; background: currentColor; flex: none; }

  /* Back */
  .card-back {
    top: 480px;
    background: linear-gradient(135deg, var(--white) 0%, var(--paper) 55%, var(--paper-shade) 100%);
    color: var(--ink-grey);
  }
  .tile-pattern {
    position: absolute; right: 0; top: 0; width: 230px; height: 354px;
    background: linear-gradient(160deg, rgba(255,255,255,.9), rgba(220,220,222,.6));
  }
  .card-back .brand {
    position: absolute; left: 150px; top: 48px; color: var(--brand-blue); font-size: 32px;
  }
  .card-back .brand-square { width: 34px; height: 34px; }
  .holder { position: absolute; left: 190px; width: 240px; top: 126px; text-align: center; }
  .holder-name { color: var(--accent-blue); font-weight: 700; font-size: 19px; letter-spacing: .5px; white-space: nowrap; }
  .holder-role { font-size: 14px; margin-top: 3px; white-space: nowrap; }
  .divider { position: absolute; height: 1px; background: var(--accent-blue); }
  .divider-top { left: 400px; right: 24px; top: 176px; }
  .divider-bottom { left: 40px; width: 330px; top: 262px; }
  .address {
    position: absolute; right: 30px; top: 192px; text-align: right;
    font-size: 14px; line-height: 1.45; white-space: nowrap;
  }
  .contacts { position: absolute; left: 40px; top: 278px; font-size: 14px; line-height: 1.6; list-style: none; }
  .contacts li { display: flex; align-items: center; gap: 9px; white-space: nowrap; }
  .contacts svg { width: 14px; height: 14px; fill: var(--accent-blue); flex: none; }
</style>
</head>
<body>
<main class="canvas">
  <section class="card card-front" aria-label="Card front">
    <div class="brand"><span class="brand-square"></span><span>RWT Fittings Ltd</span></div>
  </section>

  <section class="card card-back" aria-label="Card back">
    <div class="tile-pattern" role="img" aria-label="Soft grey tile pattern decoration"></div>
    <div class="brand"><span class="brand-square"></span><span>RWT Fittings Ltd</span></div>
    <div class="holder">
      <p class="holder-name">MARCO PELTIERI</p>
      <p class="holder-role">Owner &amp; Manager</p>
    </div>
    <div class="divider divider-top"></div>
    <p class="address">1407-5194 Linden Row<br>Burnaby BC, V5H 2K9</p>
    <div class="divider divider-bottom"></div>
    <ul class="contacts">
      <li>
        <svg viewBox="0 0 24 24" aria-hidden="true"><path d="M6.6 10.8a15.1 15.1 0 0 0 6.6 6.6l2.2-2.2a1 1 0 0 1 1-.25 11.4 11.4 0 0 0 3.6.57 1 1 0 0 1 1 1V20a1 1 0 0 1-1 1A17 17 0 0 1 3 4a1 1 0 0 1 1-1h3.5a1 1 0 0 1 1 1c0 1.25.2 2.46.57 3.6a1 1 0 0 1-.25 1z"/></svg>
        <span>16045518293</span>
      </li>
      <li>
        <svg viewBox="0 0 24 24" aria-hidden="true"><path d="M2 5h20v14H2zm2 2v.5l8 5 8-5V7zm0 2.8V17h16V9.8l-8 5z"/></svg>
        <span>RWTFittings@mailbox-demo.com</span>
      </li>
    </ul>
  </section>
</main>
</body>
</html>
```